Construction material supplies company business card ****

1. Full company name “K T Masonry Works Ltd”
I am after a Business card design for the company as a whole. We are better known in Solomon Islands as “K T Masonry” for short.

We are a building materials supplier of
Ready Mixed Concrete, Bricks and Blocks,
Quarry products- gravel, aggregates, sand etc.
Cement distributor/retailer of reputable brands.
Other prefab concrete products. Culverts, wave breakers, concrete retaining blocks etc.

2. Competitive Advantage over Competition: Quality, efficient, professional, dependable, reliable

3. We want people to feel trust worthy, high quality, strong when they see our brand

5. No preference to color. Maybe more sturdy and corporate. Not fancy.

Industry/Entity Type

CONSTRUCTION SUPPLY

Contact Information for Business Card

Name, Position, office phone mob phone, email

Requirements
Must have
• the company logo
Nice to have
• would like to see a mixture of designs, of with logo only and also with simple graphic designs to bring out the company whilst still have the strong sturdy professional feeling

```html
<!DOCTYPE html>
<html lang="en">
<head>
<meta charset="UTF-8">
<title>K T Masonry – Business Card</title>
<link rel="stylesheet" href="https://fonts.googleapis.com/css2?family=Montserrat:wght@300;400;600&family=Oswald:wght@500&display=swap">
<style>
  :root {
    --backdrop: #1a1a1a;
    --card: #1c1c1c;
    --card-edge: #2a2a2a;
    --silver: #cfcfcf;
    --silver-soft: #b5b5b5;
  }
  * { margin: 0; padding: 0; box-sizing: border-box; }
  html, body { width: 1200px; height: 900px; overflow: hidden; background: var(--backdrop); }
  .canvas {
    width: 1200px; height: 900px;
    display: flex; flex-direction: column; align-items: center; justify-content: center;
    gap: 30px;
  }
  .card {
    width: 640px; height: 366px;
    background: var(--card);
    border: 1px solid var(--card-edge);
    box-shadow: 0 10px 30px rgba(0,0,0,.55);
    display: flex; align-items: center; justify-content: center;
  }
  .brand { display: flex; align-items: center; gap: 18px; }
  .brand-mark { width: 44px; height: 44px; background: var(--silver); }
  .brand-name {
    font-family: "Montserrat", sans-serif; font-weight: 600;
    font-size: 44px; letter-spacing: 3px; color: var(--silver);
  }
  .contact-layout { display: flex; align-items: center; gap: 26px; }
  .person { text-align: right; }
  .person-name {
    font-family: "Oswald", sans-serif; font-weight: 500;
    font-size: 40px; letter-spacing: 2px; color: var(--silver); line-height: 1.05;
  }
  .person-role {
    font-family: "Montserrat", sans-serif; font-weight: 400;
    font-size: 17px; color: var(--silver-soft); margin-top: 2px;
  }
  .divider { width: 2px; height: 86px; background: var(--silver-soft); }
  .details { list-style: none; }
  .details li {
    display: flex; align-items: center; gap: 8px;
    font-family: "Montserrat", sans-serif; font-weight: 400;
    font-size: 17px; color: var(--silver); line-height: 1.5;
  }
  .details svg { width: 13px; height: 13px; flex: none; }
</style>
</head>
<body>
  <main class="canvas">
    <section class="card card-front">
      <div class="brand">
        <span class="brand-mark" aria-hidden="true"></span>
        <span class="brand-name">K T MASONRY</span>
      </div>
    </section>

    <section class="card card-back">
      <div class="contact-layout">
        <div class="person">
          <div class="person-name">DANIEL ROWE</div>
          <div class="person-role">President</div>
        </div>
        <div class="divider" aria-hidden="true"></div>
        <ul class="details">
          <li>
            <svg viewBox="0 0 16 16" aria-hidden="true"><path d="M3 1h3l1.5 4-2 1.2a9 9 0 0 0 4.3 4.3L11 8.5 15 10v3a2 2 0 0 1-2 2A12 12 0 0 1 1 3a2 2 0 0 1 2-2z" fill="#cfcfcf"/></svg>
            555-201-7734
          </li>
          <li>
            <svg viewBox="0 0 16 16" aria-hidden="true"><rect x="1" y="3" width="14" height="10" fill="none" stroke="#cfcfcf" stroke-width="1.5"/><path d="M1 3l7 6 7-6" fill="none" stroke="#cfcfcf" stroke-width="1.5"/></svg>
            info@ktmasonry.com
          </li>
          <li>
            <svg viewBox="0 0 16 16" aria-hidden="true"><circle cx="8" cy="8" r="6.5" fill="none" stroke="#cfcfcf" stroke-width="1.3"/><ellipse cx="8" cy="8" rx="3" ry="6.5" fill="none" stroke="#cfcfcf" stroke-width="1.1"/><path d="M1.5 8h13" stroke="#cfcfcf" stroke-width="1.1"/></svg>
            www.ktmasonry.com
          </li>
        </ul>
      </div>
    </section>
  </main>
</body>
</html>
```